Create a book cover for brimvale QTR

We are looking for a designer to design a cover for a log book in two versions. The two versions only have a slight difference in page count and text, other than that, it is one design.

The main color is blue. No black, no white except book title and other text. The cover must closely relate to the interior pages provided in the attachment. The style should be simple and modern, no old school graphics and fonts. Apply color psychology in the design. Please be creative and you are allowed to use download templates and graphic elements, but you must provide commercial licenses.

Here are the basic information of the book:
1. Book title: MOTOR UPKEEP TRACKING JOURNAL
2. Book size: 6x9 inches
3. Page count: 61 (version 1) and 73 (version 2)
4. Platform: brimvale qtr

Requirement for version 1:
1. Front cover: book title
2. Spine: no book title and author name
3. Back cover: text on the top and pen name logo on the bottom middle
4. Back cover text:
• Your essential tool for tracking vehicle health and maintenance
• Dedicated sections for maintenance schedules and repair history
• Track up to 30 maintenance schedules and repair history
• Easy-to-use tables and clear layouts
• Perfect for all car owners, from enthusiasts to everyday drivers

We hope it helps you keep your vehicle in excellent condition. Please take a moment to leave a positive review on Brimvale and share your experience if you find it helpful. Thank you!

Requirement for version 2:
1. Front cover: book title ,text "COLOR PAGES"
4. Back cover text:
• Track up to 36 maintenance schedules and repair history

Export:
1. Cover design in PDF and editable file format.
2. Sources/Commercial licenses for everything you did not create by yourself including fonts.

```html
<!DOCTYPE html>
<html lang="en">
<head>
<meta charset="utf-8">
<title>Motor Upkeep Tracking Journal – Cover</title>
<link href="https://fonts.googleapis.com/css2?family=Bebas+Neue&family=Montserrat:wght@500&family=Mrs+Saint+Delafield&display=swap" rel="stylesheet">
<style>
  :root {
    --navy: #001a52;
    --yellow: #fdd535;
    --white: #ffffff;
  }
  * { margin: 0; padding: 0; box-sizing: border-box; }
  html, body { width: 1200px; height: 894px; overflow: hidden; background: var(--navy); }
  .cover {
    position: relative;
    width: 1200px;
    height: 894px;
    background: var(--navy);
    color: var(--white);
  }
  .title-block {
    position: absolute;
    text-align: center;
    font-family: "Bebas Neue", sans-serif;
    line-height: 0.86;
  }
  .title-main { display: block; }
  .title-sub { display: block; }
  .title-script {
    display: block;
    font-family: "Mrs Saint Delafield", cursive;
    color: var(--yellow);
    line-height: 1;
  }

  /* Back cover */
  .back-title { left: 150px; top: 44px; width: 306px; }
  .back-title .title-main { font-size: 100px; }
  .back-title .title-sub { font-size: 46px; margin-top: 4px; }
  .back-title .title-script { font-size: 92px; margin-top: -18px; }

  .features {
    position: absolute;
    left: 30px;
    top: 304px;
    list-style: none;
    font-family: "Montserrat", sans-serif;
    font-weight: 500;
    font-size: 15px;
    line-height: 34px;
  }
  .features li::before { content: "• "; }
  .thanks {
    position: absolute;
    left: 30px;
    top: 492px;
    width: 560px;
    font-family: "Montserrat", sans-serif;
    font-weight: 500;
    font-size: 15.5px;
    line-height: 20px;
  }

  .pen-name {
    position: absolute;
    left: 0;
    width: 605px;
    top: 702px;
    display: flex;
    justify-content: center;
    align-items: center;
    gap: 10px;
    font-family: "Bebas Neue", sans-serif;
    font-size: 36px;
    color: var(--white);
  }
  .pen-name-dot { width: 14px; height: 14px; border-radius: 50%; background: var(--yellow); }

  /* Front cover */
  .front-title { left: 655px; top: 42px; width: 486px; }
  .front-title .title-main { font-size: 178px; }
  .front-title .title-sub { font-size: 80px; margin-top: 10px; }
  .front-title .title-script { font-size: 168px; margin-top: -34px; }

  .edition-label {
    position: absolute;
    left: 752px;
    top: 452px;
    width: 291px;
    height: 64px;
    background: var(--white);
    color: var(--navy);
    font-family: "Bebas Neue", sans-serif;
    font-size: 58px;
    line-height: 68px;
    text-align: center;
  }
  .emblem-art {
    position: absolute;
    left: 680px;
    top: 555px;
    width: 420px;
    height: 228px;
    border-radius: 18px;
    background: radial-gradient(ellipse at center, rgba(253,213,53,0.85), rgba(253,213,53,0.35));
  }
</style>
</head>
<body>
<main class="cover">
  <section class="back-cover">
    <h2 class="title-block back-title">
      <span class="title-main">MOTOR</span>
      <span class="title-sub">UPKEEP TRACKING</span>
      <span class="title-script">journal</span>
    </h2>
    <ul class="features">
      <li>Your essential tool for tracking vehicle health and maintenance</li>
      <li>Dedicated sections for maintenance schedules and repair history</li>
      <li>Track up to 30 maintenance schedules and repair history</li>
      <li>&nbsp;Easy-to-use tables and clear layouts</li>
      <li>&nbsp;Perfect for all car owners, from enthusiasts to everyday drivers</li>
    </ul>
    <p class="thanks">We hope it helps you keep your vehicle in excellent condition. Please take a moment to leave a positive review on Brimvale and share your experience if you find it helpful. Thank you!</p>
    <div class="pen-name"><span class="pen-name-dot"></span>TOBIAS VARGEN</div>
  </section>

  <section class="front-cover">
    <h1 class="title-block front-title">
      <span class="title-main">MOTOR</span>
      <span class="title-sub">UPKEEP TRACKING</span>
      <span class="title-script">journal</span>
    </h1>
    <div class="edition-label">COLOR PAGES</div>
    <div class="emblem-art" role="img" aria-label="Yellow icon of a car front with a gear and wrench"></div>
  </section>
</main>
</body>
</html>
```